Brightfield Ventures Inc. Letterhead

Creation of attractive and eye catching letterhead for a business start-up for the construction industry. Letterhead must relate to construction, but avoid standard hammer and tools in the design.

I forgot to add some details, sorry about that. Some pertinent info: Ph: 916-555-0187 brightfieldventures.example 448 Willowmere Ave, Ste 210 Folsom, CA 95999 info@brightfieldventures.example not sure if slogan should be in there" “Connecting construction professionals to create a purpose driven industry.” must be able to be used in word. Thanks!

```html
<!DOCTYPE html>
<html lang="en">
<head>
<meta charset="utf-8">
<title>Brightfield Ventures Inc. Letterhead</title>
<link href="https://fonts.googleapis.com/css2?family=Arimo:wght@400;700&family=Montserrat:wght@500&family=Open+Sans:wght@400;700&display=swap" rel="stylesheet">
<style>
  :root {
    --brand-red: #c4161c;
    --brand-navy: #1f2a5c;
    --ink: #111111;
    --muted: #333333;
    --paper: #ffffff;
    --backdrop: #e3e4e4;
  }
  html, body {
    margin: 0;
    padding: 0;
    width: 1200px;
    height: 945px;
    overflow: hidden;
    background: var(--backdrop);
  }
  .letterhead {
    position: absolute;
    left: 280px;
    top: 18px;
    width: 640px;
    height: 909px;
    background: var(--paper);
    box-shadow: 0 2px 10px rgba(0,0,0,0.12);
    font-family: "Arimo", Arial, sans-serif;
    color: var(--ink);
  }
  .header-rule {
    position: absolute;
    left: 0;
    top: 0;
  }
  .brand {
    position: absolute;
    left: 40px;
    top: 118px;
    display: flex;
    align-items: center;
    gap: 10px;
  }
  .brand-dot {
    width: 22px;
    height: 22px;
    border-radius: 50%;
    background: var(--brand-red);
  }
  .brand-name {
    font-family: "Montserrat", sans-serif;
    font-weight: 500;
    font-size: 17px;
    letter-spacing: 1.5px;
    color: var(--brand-navy);
    text-transform: uppercase;
  }
  .contact {
    position: absolute;
    right: 34px;
    top: 26px;
    font-family: "Open Sans", sans-serif;
    font-size: 8.5px;
    color: var(--muted);
    text-align: right;
    line-height: 14px;
  }
  .contact-line {
    display: flex;
    justify-content: flex-end;
    align-items: center;
    gap: 4px;
  }
  .contact-icon {
    width: 10px;
    height: 10px;
    border-radius: 50%;
    background: var(--brand-red);
    display: inline-flex;
    align-items: center;
    justify-content: center;
  }
  .address {
    position: absolute;
    left: 330px;
    top: 84px;
    font-family: "Open Sans", sans-serif;
    font-size: 8px;
    color: var(--muted);
  }
  .website {
    position: absolute;
    right: 34px;
    top: 104px;
    font-family: "Open Sans", sans-serif;
    font-size: 10px;
    font-weight: 700;
    color: var(--brand-navy);
    letter-spacing: 0.5px;
  }
  .website .domain { color: var(--brand-red); }
  .letter-body {
    position: absolute;
    left: 70px;
    top: 250px;
    width: 500px;
    font-size: 11.5px;
    line-height: 16px;
  }
  .recipient { margin: 0 0 6px; }
  .letter-body p.paragraph {
    margin: 0 0 22px;
    text-indent: 0;
  }
  .sign-off {
    position: absolute;
    left: 70px;
    top: 700px;
    font-size: 11.5px;
  }
  .signature-area {
    width: 120px;
    height: 40px;
    margin: 4px 0 6px;
    background: linear-gradient(90deg, #f2f2f2, #e4e4e4);
    border-radius: 4px;
  }
  .signer { font-weight: 700; font-size: 12px; }
  .footer-band {
    position: absolute;
    left: 0;
    bottom: 0;
    width: 100%;
    height: 6px;
    background: var(--brand-red);
  }
</style>
</head>
<body>
<main class="letterhead">
  <svg class="header-rule" width="640" height="170" viewBox="0 0 640 170" aria-hidden="true">
    <polyline points="20,158 300,158 326,124 420,124" fill="none" stroke="var(--brand-red)" stroke-width="2"/>
  </svg>

  <div class="brand">
    <span class="brand-dot"></span>
    <span class="brand-name">Brightfield Ventures</span>
  </div>

  <div class="contact">
    <div class="contact-line">1-916-555-0187
      <span class="contact-icon"><svg width="6" height="6" viewBox="0 0 10 10"><path d="M2 1 L4 1 L5 3 L4 4 Q5 6 6 6 L7 5 L9 6 L9 8 Q8 9 7 9 Q1 8 1 3 Q1 2 2 1Z" fill="#fff"/></svg></span>
    </div>
    <div class="contact-line">info@brightfieldventures.example
      <span class="contact-icon"><svg width="6" height="6" viewBox="0 0 10 10"><rect x="1" y="2" width="8" height="6" fill="none" stroke="#fff" stroke-width="1.3"/><polyline points="1,2 5,5.5 9,2" fill="none" stroke="#fff" stroke-width="1.2"/></svg></span>
    </div>
  </div>
  <div class="address">448 Willowmere Ave, Ste 210, Folsom, CA 95999</div>
  <div class="website">www.<span class="domain">brightfieldventures</span>.example</div>

  <section class="letter-body">
    <p class="recipient">Lorem Ipsum<br>Lorem Ipsum Admin</p>
    <p class="paragraph">Lorem Ipsum is simply dummy text of the printing and typesetting industry. Lorem Ipsum has been the industry's standard dummy text ever since the 1500s, when an unknown printer took a galley of type and scrambled it to make a type specimen book. It has survived not only five centuries, but also the leap into electronic typesetting, remaining essentially unchanged.</p>
    <p class="paragraph">Lorem Ipsum is simply dummy text of the printing and typesetting industry. Lorem Ipsum has been the industry's standard dummy text ever since the 1500s, when an unknown printer took a galley of type and scrambled it to make a type specimen book.</p>
    <p class="paragraph">It has survived not only five centuries, but also the leap into electronic typesetting, remaining essentially unchanged. Lorem Ipsum is simply dummy text of the printing and typesetting industry. Lorem Ipsum has been the industry's standard dummy text ever since the 1500s, when an unknown printer took a galley of type and scrambled</p>
    <p class="paragraph">Lorem Ipsum is simply dummy text of the printing and typesetting industry. Lorem Ipsum has been the industry's standard dummy text ever since the 1500s, when an unknown printer took a galley of type and scrambled it to make a type specimen book. It has survived not only five centuries, but also the leap into electronic typesetting, remaining essentially unchanged.</p>
  </section>

  <div class="sign-off">
    <div>Lorem Ipsum</div>
    <div class="signature-area" role="img" aria-label="Handwritten signature"></div>
    <div class="signer">Lorem Ipsum Admin</div>
  </div>

  <div class="footer-band"></div>
</main>
</body>
</html>
```